Maple Lantern Productions web site

I need to build a website for a new company I am launching next month. Maple Lantern Productions is a company based in New England that provides sound, lighting, and audio visual services to weddings, corporate, and any other cusomer base looking for quality service for a fair price. Looking for somebody to do a full site not just the image files. I am looking to keep the colors of my logo (orange and black) and possibly grey and white. I am looking to build my site very similar to brightvaleevents.example, which is owned by a friend of mine. I like how he has the big pictures that load in to the site and the basic menu items. I'll need a gallery of photos. The designs should communicate quality, value and trust.
My website address is maplelanternco.example.
Updates

Hi and thanks to everyone for posting such great ideas for our new design.I have some items that I'd like to ask you all to focus on in your revisions.I like how http://www.brightvaleevents.example/ website has five or six high res pictures that change in a slideshow format with a caption that loads in for each one for the different types of services. Try and capture pics like these and with teh same headings as he has. The basic menu designs have been interesting.I am more fond of the menus that are more white with some orange as I dont want it to be too dark. I'm curious to see how your galleries will work and if i'll be able to edit the pages myself? I have some more info on the company for you to fill in:website address is ciderhouseco.comemail: info@ciderhouseco.comaddress: Maple Lantern Productions57 Littlefield StreetAvon, MA 02417"New England's finest DJ's, lighting and sound, video and more. Creating memories one perfect event at a time."Put this under the loading pictures as a tagline.About Cider HouseCider House Productions is a collection of New England's finest talent, ready to make your next event the one you've dreamed of. We have the skills and expertise to deliver your vision of your perfect event. From elegant weddings to themed mitzvah's, corporate av, videography and detail lighting, we offer all of the elements to make your event a success. Added Wednesday, March 1, 2017

Designer's Please also make sure that your design flows well on any device it is being viewed on as well. Thanks. Added Wednesday, March 1, 2017

Project Deadline Extended Reason: Hello designerThank you all very much for your hard work on our project. Im sorry but i need to extend the date of my project. Our parent conpany Rook Nine Prodactions sponsors Bay Youth Assemblies and we are currently at their leadership conference on the Cape. I will be back in on Monday and with your help will get this finished by Thursday the 16th. Thanks Added Thursday, March 9, 2017

Project Deadline Extended Reason: One of the designers is not responding so I now have to make revisions with other designers. I hope to get this website done over the weekends so please get your revisions as soon as possible. Thank you. I am also upgrading the budget another $75 to hopefully get some more interest on my project. Added Wednesday, March 15, 2017

Target Market(s)

Wedding - Corporate -

Industry/Entity Type

It Company

Coding

Coded - Design and coding required

Number of Pages Required

5+ page

Font styles to use
Sans Serif

Requirements
Must have
• Photo Gallery - I want to be able to edit it myself
Nice to have
• I like the look of my friends website brightvaleevents.example

```html
<!DOCTYPE html>
<html lang="en">
<head>
<meta charset="utf-8">
<title>Maple Lantern Productions</title>
<link rel="stylesheet" href="https://fonts.googleapis.com/css2?family=Lato:wght@300;400;700&display=swap">
<style>
:root{
  --orange:#e8692a;
  --orange-dark:#c9531c;
  --ink:#222222;
  --grey:#777777;
  --light:#f4f4f4;
  --white:#ffffff;
  --night:#15171c;
}
*{box-sizing:border-box;margin:0;padding:0}
html,body{width:1200px;height:2508px;overflow:hidden}
body{font-family:'Lato',Arial,sans-serif;color:var(--ink);background:var(--white);position:relative}
.section-title{font-weight:300;font-size:30px;letter-spacing:1px;text-align:center;text-transform:uppercase}

/* Header + hero */
.hero{position:absolute;left:0;top:0;width:1200px;height:612px;
  background:
    radial-gradient(ellipse 260px 200px at 48% 22%,rgba(250,250,248,.95) 0%,rgba(235,230,222,.7) 45%,rgba(235,230,222,0) 100%),
    radial-gradient(ellipse 180px 160px at 66% 38%,rgba(60,40,30,.9) 0%,rgba(60,40,30,0) 100%),
    radial-gradient(ellipse 140px 90px at 60% 58%,rgba(230,170,110,.55) 0%,rgba(230,170,110,0) 100%),
    radial-gradient(ellipse 420px 260px at 18% 70%,rgba(150,120,90,.55) 0%,rgba(150,120,90,0) 100%),
    radial-gradient(ellipse 360px 240px at 88% 75%,rgba(170,130,90,.5) 0%,rgba(170,130,90,0) 100%),
    linear-gradient(180deg,#8c7a66 0%,#6a5643 45%,#3d2f24 100%)}
.hero-shade{position:absolute;inset:0;background:linear-gradient(90deg,rgba(20,14,10,.45) 0%,rgba(20,14,10,.1) 55%,rgba(20,14,10,0) 100%)}
.site-header{position:absolute;left:0;top:0;width:1200px;height:56px;background:rgba(255,255,255,.18);
  display:flex;align-items:center;justify-content:space-between;padding:0 40px 0 28px}
.brand{display:flex;align-items:center;gap:10px;color:var(--white);font-weight:700;font-size:17px;letter-spacing:1px;text-transform:uppercase}
.brand-dot{width:26px;height:26px;border-radius:50%;background:var(--orange)}
.main-nav{display:flex;gap:26px}
.main-nav a{color:var(--white);font-size:11px;letter-spacing:1px;text-decoration:none;text-transform:uppercase}
.main-nav a.active{color:var(--orange)}
.hero-copy{position:absolute;left:100px;top:316px;width:720px;color:var(--white)}
.hero-copy h1{font-weight:400;font-size:36px;line-height:1.15;text-transform:uppercase;letter-spacing:1px}
.hero-copy p{margin-top:14px;font-size:13px;line-height:1.55;width:430px}
.btn{display:inline-block;background:var(--orange);color:var(--white);font-size:11px;letter-spacing:1px;text-transform:uppercase;padding:10px 22px;border-radius:2px;text-decoration:none}
.hero-copy .btn{margin-top:28px}
.arrow{position:absolute;width:20px;height:40px}

/* Services */
.services{position:absolute;left:0;top:612px;width:1200px;height:538px;background:var(--white)}
.services .section-title{margin-top:50px}
.title-rule{width:1000px;height:1px;background:#dddddd;margin:16px auto 0}
.service-grid{display:flex;gap:20px;margin:24px 0 0 100px}
.service{width:320px}
.service-photo{height:176px}
.service h3{margin-top:26px;color:var(--orange);font-weight:400;font-size:15px;letter-spacing:1px;text-transform:uppercase}
.service p{margin-top:10px;font-size:11.5px;line-height:1.6;color:var(--grey)}
.service .more{display:inline-block;margin-top:14px;font-size:10px;color:var(--orange);text-transform:uppercase;letter-spacing:1px}

/* Gallery */
.gallery{position:absolute;left:0;top:1150px;width:1200px;height:450px;
  background:
    radial-gradient(ellipse 220px 120px at 30% 28%,rgba(190,200,230,.28) 0%,rgba(190,200,230,0) 100%),
    radial-gradient(ellipse 260px 130px at 70% 22%,rgba(220,210,240,.22) 0%,rgba(220,210,240,0) 100%),
    radial-gradient(ellipse 700px 160px at 50% 100%,rgba(0,0,0,.7) 0%,rgba(0,0,0,0) 100%),
    linear-gradient(180deg,#23252d 0%,#33323c 45%,#16161b 100%)}
.gallery .section-title{color:var(--white);margin-top:56px}
.gallery-row{display:flex;gap:20px;margin:32px 0 0 100px}
.gallery-item{width:320px;height:236px;border:3px solid var(--white)}

/* Reviews */
.reviews{position:absolute;left:0;top:1600px;width:1200px;height:410px;background:var(--white);text-align:center}
.reviews .section-title{margin-top:52px}
.avatar{width:96px;height:96px;border-radius:50%;margin:28px auto 0;background:radial-gradient(circle at 50% 40%,#c7a98c 0%,#8a6a52 55%,#3a3430 100%);border:3px solid #eeeeee}
.review-text{width:1000px;margin:30px auto 0;font-size:12px;line-height:1.7;color:var(--grey)}
.reviewer{margin-top:24px;font-size:12px;color:var(--orange)}

/* Contact */
.contact{position:absolute;left:0;top:2010px;width:1200px;height:498px;
  background:
    radial-gradient(ellipse 300px 90px at 20% 78%,rgba(230,150,70,.35) 0%,rgba(230,150,70,0) 100%),
    radial-gradient(ellipse 340px 90px at 75% 82%,rgba(240,170,90,.3) 0%,rgba(240,170,90,0) 100%),
    radial-gradient(ellipse 500px 120px at 50% 66%,rgba(120,130,170,.25) 0%,rgba(120,130,170,0) 100%),
    linear-gradient(180deg,#1e2129 0%,#282a33 50%,#3a2d22 80%,#1b1a1e 100%)}
.contact .section-title{color:var(--white);margin-top:62px}
.contact-form{position:absolute;left:100px;top:132px;width:540px}
.field-row{display:flex;gap:20px}
.field{background:var(--white);height:34px;flex:1;font-size:11px;color:var(--grey);padding:10px 12px}
.field.message{height:116px;margin-top:16px}
.contact-form .btn{position:absolute;right:0;top:188px;width:110px;text-align:center}
.map{position:absolute;left:670px;top:132px;width:430px;height:220px;
  background:
    radial-gradient(ellipse 260px 200px at 95% 40%,#7fa9dc 0%,#93b9e3 55%,rgba(147,185,227,0) 100%),
    linear-gradient(110deg,#ece8df 0%,#e4dfd4 50%,#d9d5cb 100%);border:3px solid var(--white)}
.socials{position:absolute;left:0;top:412px;width:1200px;display:flex;justify-content:center;gap:8px}
.social{width:18px;height:18px;border-radius:50%}
.copyright{position:absolute;left:0;top:458px;width:1200px;text-align:center;font-size:10px;color:#bbbbbb}
</style>
</head>
<body>

<section class="hero" role="img" aria-label="Photo of a bride and groom dancing on a patterned floor">
  <div class="hero-shade"></div>
  <header class="site-header">
    <div class="brand"><span class="brand-dot"></span>Maple Lantern Productions</div>
    <nav class="main-nav">
      <a href="#" class="active">About Us</a>
      <a href="#">Services</a>
      <a href="#">Gallery</a>
      <a href="#">References</a>
      <a href="#">Contact</a>
    </nav>
  </header>
  <svg class="arrow" style="left:18px;top:286px" viewBox="0 0 20 40"><polyline points="16,2 4,20 16,38" fill="none" stroke="#fff" stroke-width="2"/></svg>
  <svg class="arrow" style="right:18px;top:286px" viewBox="0 0 20 40"><polyline points="4,2 16,20 4,38" fill="none" stroke="#fff" stroke-width="2"/></svg>
  <div class="hero-copy">
    <h1>Welcome to<br>Maple Lantern Productions</h1>
    <p>"The Northeast's brightest DJ's, lighting and sound, video and more. Shaping moments one flawless night at a time."</p>
    <a href="#" class="btn">Read More</a>
  </div>
</section>

<section class="services">
  <h2 class="section-title">Our Services</h2>
  <div class="title-rule"></div>
  <div class="service-grid">
    <article class="service">
      <div class="service-photo" role="img" aria-label="Photo of a DJ booth lit in orange" style="background:radial-gradient(ellipse 120px 80px at 40% 45%,rgba(255,190,110,.85) 0%,rgba(255,190,110,0) 100%),radial-gradient(ellipse 90px 60px at 78% 30%,rgba(240,120,60,.7) 0%,rgba(240,120,60,0) 100%),linear-gradient(180deg,#2a1a16 0%,#4a2a1e 60%,#1c1412 100%)"></div>
      <h3>Sound</h3>
      <p>Crisp, balanced sound for ceremonies, speeches and dance floors, with clear wireless mics, full-range speakers and a technician on site all night.</p>
      <a class="more">Read More</a>
    </article>
    <article class="service">
      <div class="service-photo" role="img" aria-label="Photo of candlelit glasses on a reception table" style="background:radial-gradient(ellipse 110px 60px at 35% 55%,rgba(255,225,170,.95) 0%,rgba(255,225,170,0) 100%),radial-gradient(ellipse 100px 60px at 72% 50%,rgba(250,205,140,.85) 0%,rgba(250,205,140,0) 100%),linear-gradient(180deg,#6a4a30 0%,#a37a52 50%,#3e2a1c 100%)"></div>
      <h3>Lighting</h3>
      <p>Uplighting, pin spots and dance lighting that set the mood of your room, tuned to your colours and changing with every moment of the night.</p>
      <a class="more">Read More</a>
    </article>
    <article class="service">
      <div class="service-photo" role="img" aria-label="Photo of a banquet hall with pink lighting" style="background:radial-gradient(ellipse 160px 60px at 50% 75%,rgba(255,255,255,.85) 0%,rgba(255,255,255,0) 100%),radial-gradient(ellipse 200px 80px at 50% 20%,rgba(235,120,150,.8) 0%,rgba(235,120,150,0) 100%),linear-gradient(180deg,#e9a3ad 0%,#f2c9c9 55%,#f8e6e2 100%)"></div>
      <h3>Audio Visual</h3>
      <p>Projectors, screens and live video for presentations, slideshows and corporate events, set up and run by our crew so everything plays on cue.</p>
      <a class="more">Read More</a>
    </article>
  </div>
</section>

<section class="gallery" role="img" aria-label="Background photo of a concert crowd with raised hands">
  <h2 class="section-title">Our Gallery</h2>
  <svg class="arrow" style="left:22px;top:182px" viewBox="0 0 20 40"><polyline points="16,2 4,20 16,38" fill="none" stroke="#fff" stroke-width="2"/></svg>
  <svg class="arrow" style="right:22px;top:182px" viewBox="0 0 20 40"><polyline points="4,2 16,20 4,38" fill="none" stroke="#fff" stroke-width="2"/></svg>
  <div class="gallery-row">
    <div class="gallery-item" role="img" aria-label="Photo of a table with purple uplighting" style="background:radial-gradient(ellipse 110px 70px at 55% 60%,rgba(255,235,250,.9) 0%,rgba(255,235,250,0) 100%),radial-gradient(ellipse 140px 90px at 20% 25%,rgba(200,90,220,.8) 0%,rgba(200,90,220,0) 100%),linear-gradient(180deg,#2c1438 0%,#6b2f86 50%,#3a1a48 100%)"></div>
    <div class="gallery-item" role="img" aria-label="Photo of a couple walking through a lit hall" style="background:radial-gradient(ellipse 60px 100px at 50% 60%,rgba(245,240,230,.9) 0%,rgba(245,240,230,0) 100%),radial-gradient(ellipse 160px 60px at 50% 15%,rgba(240,200,140,.5) 0%,rgba(240,200,140,0) 100%),linear-gradient(180deg,#2a2320 0%,#54463a 55%,#2a221c 100%)"></div>
    <div class="gallery-item" role="img" aria-label="Photo of a white table setting with glasses" style="background:radial-gradient(ellipse 140px 80px at 50% 70%,rgba(255,255,255,.95) 0%,rgba(255,255,255,0) 100%),radial-gradient(ellipse 140px 80px at 30% 25%,rgba(120,150,200,.7) 0%,rgba(120,150,200,0) 100%),linear-gradient(180deg,#9fb0c8 0%,#d6dde8 55%,#eef0f3 100%)"></div>
  </div>
</section>

<section class="reviews">
  <h2 class="section-title">Client Reviews</h2>
  <div class="avatar" role="img" aria-label="Client portrait"></div>
  <svg class="arrow" style="left:22px;top:186px" viewBox="0 0 20 40"><polyline points="16,2 4,20 16,38" fill="none" stroke="#999" stroke-width="2"/></svg>
  <svg class="arrow" style="right:22px;top:186px" viewBox="0 0 20 40"><polyline points="4,2 16,20 4,38" fill="none" stroke="#999" stroke-width="2"/></svg>
  <p class="review-text">From the first call to the last song, the team was calm, friendly and completely prepared. The sound was perfect during our vows, the lighting turned the hall into something magical, and the dance floor never emptied. Every guest asked who ran the night. We would book them again for any event, big or small, without a second thought.</p>
  <p class="reviewer">John Doe</p>
</section>

<section class="contact" role="img" aria-label="Background photo of a city skyline at night">
  <h2 class="section-title">Contact</h2>
  <form class="contact-form">
    <div class="field-row">
      <div class="field">Name</div>
      <div class="field">Email</div>
    </div>
    <div class="field message">Message</div>
    <a href="#" class="btn">Submit</a>
  </form>
  <div class="map" role="img" aria-label="Map of the company location"></div>
  <div class="socials">
    <span class="social" style="background:#5b7fc4"></span>
    <span class="social" style="background:#4db3e6"></span>
    <span class="social" style="background:var(--orange)"></span>
  </div>
  <p class="copyright">© 2017 maplelanternco.example. All Rights Reserved.</p>
</section>

</body>
</html>
```